Landing Page / Waitlist

I would like a landing page for people to sign up for a waiting list. The text on the page should include (but is not limited to):
1) Main point: The accounting system you'll love
2) Secondary points:
a. Ruthlessly efficient
b. Quietly intelligent
c. Driven by AI
I've attached a file of our logo

The design should be simple, clean, and innovative - this is an ai company

```html
<!DOCTYPE html>
<html lang="en">
<head>
<meta charset="UTF-8">
<title>LedgerLume — Join the Waitlist</title>
<link rel="stylesheet" href="https://fonts.googleapis.com/css2?family=Montserrat:wght@700&family=Lato:wght@400;700&display=swap">
<style>
  :root {
    --page-bg: #eef0f3;
    --ink: #0d0d0d;
    --text-muted: #444a50;
    --brand-grey: #7b7d80;
    --brand-blue: #1b9af0;
    --button-top: #00c0fb;
    --button-bottom: #0096f5;
    --field-border: #a9adb2;
    --field-bg: #f2f3f5;
    --photo-light: #f4f5f7;
    --photo-mid: #d9dce0;
    --photo-dark: #b9bcc1;
  }

  * { box-sizing: border-box; margin: 0; padding: 0; }

  html, body {
    width: 1200px;
    height: 600px;
    overflow: hidden;
  }

  body {
    background: var(--page-bg);
    font-family: "Lato", Arial, sans-serif;
    position: relative;
  }

  .hero-photo {
    position: absolute;
    left: 0;
    top: 0;
    width: 460px;
    height: 600px;
    background:
      radial-gradient(ellipse at 20% 18%, var(--photo-dark) 0%, var(--photo-mid) 35%, transparent 70%),
      radial-gradient(ellipse at 30% 75%, var(--photo-mid) 0%, transparent 60%),
      linear-gradient(90deg, var(--photo-mid) 0%, var(--photo-light) 80%, var(--page-bg) 100%);
  }

  .signup-panel {
    position: absolute;
    left: 549px;
    top: 0;
    width: 545px;
    height: 600px;
    text-align: center;
  }

  .brand {
    position: absolute;
    top: 150px;
    left: 0;
    width: 100%;
    display: flex;
    justify-content: center;
    align-items: center;
    gap: 10px;
  }

  .brand-mark {
    width: 26px;
    height: 26px;
    background: var(--brand-blue);
  }

  .brand-name {
    font-family: "Lato", Arial, sans-serif;
    font-weight: 700;
    font-size: 36px;
    color: var(--brand-grey);
    letter-spacing: -0.5px;
  }

  .headline {
    position: absolute;
    top: 224px;
    left: 0;
    width: 100%;
    font-family: "Montserrat", Arial, sans-serif;
    font-weight: 700;
    font-size: 40px;
    line-height: 43px;
    color: var(--ink);
  }

  .tagline {
    position: absolute;
    top: 322px;
    left: 0;
    width: 100%;
    font-size: 22px;
    color: var(--text-muted);
  }

  .waitlist-form {
    position: absolute;
    top: 376px;
    left: 0;
    width: 545px;
    height: 60px;
    display: flex;
  }

  .email-field {
    width: 331px;
    height: 60px;
    border: 1px solid var(--field-border);
    border-right: none;
    border-radius: 2px 0 0 2px;
    background: var(--field-bg);
    padding: 0 20px;
    font-family: "Lato", Arial, sans-serif;
    font-size: 19px;
    color: var(--text-muted);
    outline: none;
  }

  .email-field::placeholder { color: var(--text-muted); }

  .join-button {
    width: 214px;
    height: 60px;
    border: none;
    border-radius: 0 2px 2px 0;
    background: linear-gradient(180deg, var(--button-top), var(--button-bottom));
    color: #ffffff;
    font-family: "Lato", Arial, sans-serif;
    font-size: 22px;
  }

  .copyright {
    position: absolute;
    top: 477px;
    left: 0;
    width: 100%;
    font-size: 15px;
    color: var(--text-muted);
  }
</style>
</head>
<body>
  <div class="hero-photo" role="img" aria-label="Top-down photo of a white desk with a laptop, tablet, glasses, a cup of coffee, paper clips, a notebook with pen and sticky notes"></div>

  <main class="signup-panel">
    <div class="brand">
      <span class="brand-mark"></span>
      <span class="brand-name">LedgerLume</span>
    </div>

    <h1 class="headline">The Accounting System<br>You'll Love</h1>

    <p class="tagline">Ruthlessly efficient. Quietly intelligent. Driven by AI.</p>

    <form class="waitlist-form" action="#">
      <input class="email-field" type="email" placeholder="Email" aria-label="Email">
      <button class="join-button" type="button">Join the Waitlist</button>
    </form>

    <p class="copyright">Copyright © 2025 LedgerLume. All rights reserved.</p>
  </main>
</body>
</html>
```